Support People to improve their image and well-being by provided personalised advise

We need a design for business cards that could be used for production on plano press. We build a new business in our region for advising mostly women (also men though) on style embracing several aspects including fashion, style, self-confidence and ultimately your internal and external image. The business card should be "classy", "french-style". The business is located in the french -speaking part of Switzerland, close to France. The name of the company is Lomu Grace

Target Market(s)

Service fees won't be cheap (medium to premium) thus we target mid-class to upper-class women (1st target) and men (2nd target)

Industry/Entity Type

Life Coaching

Contact Information for Business Card

Conseil en Image

+41 76 418 63 07
tovasel@lomu-grace.example
linkedin.example/in/sel-moran-tova

Logo Text

Lomu Grace

Colors

Designer to choose colors to be used in the design.

```html
<!DOCTYPE html>
<html lang="fr">
<head>
<meta charset="utf-8">
<title>Lomu Grace – Cartes de visite</title>
<link rel="stylesheet" href="https://fonts.googleapis.com/css2?family=Questrial&display=swap">
<style>
  :root {
    --backdrop: #bdbdbd;
    --blush: #d86a6a;
    --paper: #f4f4f4;
    --ink: #333333;
    --accent-text: #d65f5f;
  }
  * { margin: 0; padding: 0; box-sizing: border-box; }
  html, body {
    width: 1200px;
    height: 576px;
    overflow: hidden;
    background: var(--backdrop);
  }
  body {
    position: relative;
    font-family: "Questrial", "Century Gothic", sans-serif;
    color: var(--ink);
  }
  .card {
    position: absolute;
    top: 138px;
    width: 484px;
    height: 294px;
    border-radius: 14px;
  }
  .card--front {
    left: 82px;
    background: var(--blush);
    display: flex;
    align-items: center;
    justify-content: center;
  }
  .card--back {
    left: 602px;
    background: var(--paper);
  }
  .brand-name {
    font-weight: 400;
    color: var(--ink);
    white-space: nowrap;
    letter-spacing: 0.5px;
  }
  .card--front .brand-name {
    font-size: 40px;
    margin-top: 12px;
  }
  .card--back .brand-name {
    position: absolute;
    right: 38px;
    bottom: 56px;
    font-size: 28px;
  }
  .holder {
    position: absolute;
    left: 34px;
    top: 52px;
  }
  .holder__name {
    font-size: 20px;
    color: var(--accent-text);
    line-height: 1.1;
  }
  .holder__role {
    font-size: 12px;
    margin-top: 3px;
  }
  .contacts {
    position: absolute;
    left: 34px;
    top: 206px;
    list-style: none;
    font-size: 13px;
  }
  .contacts li {
    display: flex;
    align-items: center;
    height: 18px;
  }
  .contacts svg {
    width: 11px;
    height: 11px;
    margin-right: 13px;
    fill: var(--accent-text);
    flex: none;
  }
</style>
</head>
<body>
  <section class="card card--front" aria-label="Recto">
    <span class="brand-name">Lomu Grace</span>
  </section>

  <section class="card card--back" aria-label="Verso">
    <div class="holder">
      <p class="holder__name">Tova Sel Moran</p>
      <p class="holder__role">Managing Director</p>
    </div>

    <ul class="contacts">
      <li>
        <svg viewBox="0 0 12 12" aria-hidden="true">
          <path d="M1 4.2c0-1.3 2.2-2.2 5-2.2s5 .9 5 2.2v.8H8.4v-1H3.6v1H1z"/>
          <path d="M3.2 5.5h5.6l1.4 4.5H1.8z"/>
        </svg>
        +41 76 418 63 07
      </li>
      <li>
        <svg viewBox="0 0 12 12" aria-hidden="true">
          <path d="M1 2.5h10v7H1z M1.6 3.1 6 6.6l4.4-3.5" stroke="#f4f4f4" stroke-width="0.8"/>
        </svg>
        tovasel@lomu-grace.example
      </li>
      <li>
        <svg viewBox="0 0 12 12" aria-hidden="true">
          <circle cx="6" cy="6" r="5"/>
          <path d="M1 6h10M6 1v10M6 1c-2.2 2.5-2.2 7.5 0 10M6 1c2.2 2.5 2.2 7.5 0 10" stroke="#f4f4f4" stroke-width="0.7" fill="none"/>
        </svg>
        www.lomu-grace.example
      </li>
    </ul>

    <span class="brand-name">Lomu Grace</span>
  </section>
</body>
</html>
```